Verodex business card

Business card for sustainable investment company called "Verodex". Verodex is an exchange platform selling carbon credits between buyers and sellers. Carbon Credits are an environmental commodity for reducing global carbon emissions.

the card should obviously have our logo and the theme should be sustainability/environment mixed with a trading platform.

Contact Information for Business Card

Logo, Name, Title, Phone, Email

Colors
0054AA
0677BA
7BADD7
CADEEF
E8F1F8
0094D4
00A9DD
6FCCEA
C7EBF8
E9F6FB
00AB8E
00BBA5
67D7C9
C6EFE9
E9F9F6
59FF00
82FF00
B8FF75
E3FFCB
F4FFEA

```html
<!DOCTYPE html>
<html lang="en">
<head>
<meta charset="UTF-8">
<title>Verodex Business Card</title>
<link href="https://fonts.googleapis.com/css2?family=Montserrat:wght@400;500;600;700&display=swap" rel="stylesheet">
<style>
  :root {
    --bg: #ced1d1;
    --card: #1b1b1d;
    --card-edge: #0d0d0f;
    --ink-light: #e6e8ea;
    --brand-blue: #1f86c4;
    --brand-deep: #0054AA;
    --rule: #1a78b4;
  }
  * { margin: 0; padding: 0; box-sizing: border-box; }
  html, body {
    width: 1200px;
    height: 1050px;
    overflow: hidden;
    background: var(--bg);
    font-family: "Montserrat", sans-serif;
  }
  .sheet {
    width: 1200px;
    height: 1050px;
    display: flex;
    flex-direction: column;
    align-items: center;
    justify-content: center;
    gap: 40px;
  }
  .card {
    position: relative;
    width: 800px;
    height: 457px;
    background: radial-gradient(circle at 30% 25%, #242427 0%, var(--card) 60%, #161618 100%);
    border-radius: 4px;
    box-shadow: 0 10px 24px rgba(0,0,0,0.18);
    border-bottom: 2px solid var(--card-edge);
    overflow: hidden;
  }
  .brand {
    display: flex;
    align-items: center;
    gap: 14px;
  }
  .brand-dot {
    border-radius: 50%;
    background: var(--brand-blue);
    flex-shrink: 0;
  }
  .brand-name {
    font-weight: 600;
    color: var(--ink-light);
    letter-spacing: 0.02em;
    line-height: 1;
  }

  /* contact side */
  .card-contact .brand {
    position: absolute;
    left: 54px;
    top: 170px;
  }
  .card-contact .brand-dot { width: 36px; height: 36px; }
  .card-contact .brand-name { font-size: 40px; }
  .divider {
    position: absolute;
    left: 392px;
    top: 96px;
    width: 2px;
    height: 250px;
    background: var(--rule);
  }
  .details {
    position: absolute;
    left: 424px;
    top: 98px;
    color: var(--ink-light);
  }
  .person-name {
    font-size: 30px;
    font-weight: 700;
    color: var(--brand-blue);
    letter-spacing: 0.04em;
    text-transform: uppercase;
    line-height: 1.05;
  }
  .person-title {
    font-size: 18px;
    font-weight: 500;
    text-transform: uppercase;
    letter-spacing: 0.03em;
    margin-bottom: 18px;
  }
  .address {
    font-size: 17px;
    line-height: 1.35;
    margin-bottom: 18px;
    font-weight: 500;
  }
  .contact-list { list-style: none; }
  .contact-list li {
    display: flex;
    align-items: center;
    gap: 10px;
    font-size: 17px;
    font-weight: 500;
    line-height: 1.6;
  }
  .contact-list svg { width: 15px; height: 15px; flex-shrink: 0; }

  /* logo side */
  .card-logo .brand {
    position: absolute;
    inset: 0;
    justify-content: center;
    gap: 24px;
  }
  .card-logo .brand-dot { width: 72px; height: 72px; }
  .card-logo .brand-name { font-size: 84px; }
</style>
</head>
<body>
  <main class="sheet">
    <section class="card card-contact" aria-label="Business card, contact side">
      <div class="brand">
        <span class="brand-dot"></span>
        <span class="brand-name">VERODEX</span>
      </div>
      <div class="divider"></div>
      <div class="details">
        <h1 class="person-name">Dana Whitlow</h1>
        <p class="person-title">Manager</p>
        <p class="address">2215 Alder Ridge Rd. Suite 40<br>Lakeview, OR 97630</p>
        <ul class="contact-list">
          <li>
            <svg viewBox="0 0 16 16" aria-hidden="true"><path fill="var(--brand-blue)" d="M3.6 1.5 5.8 1l1.3 3.2-1.6 1.2a8 8 0 0 0 5.1 5.1l1.2-1.6L15 10.2l-.5 2.2c-.2.8-1 1.3-1.8 1.2C6.8 13 3 9.2 2.4 3.3c-.1-.8.4-1.6 1.2-1.8z"/></svg>
            555-014-2290
          </li>
          <li>
            <svg viewBox="0 0 16 16" aria-hidden="true"><rect x="1" y="3" width="14" height="10" rx="1" fill="var(--brand-blue)"/><path d="M1.5 3.8 8 8.6l6.5-4.8" fill="none" stroke="var(--card)" stroke-width="1.3"/></svg>
            hello@verodex.com
          </li>
          <li>
            <svg viewBox="0 0 16 16" aria-hidden="true"><g fill="none" stroke="var(--brand-blue)" stroke-width="1.4"><circle cx="8" cy="8" r="6.5"/><ellipse cx="8" cy="8" rx="3" ry="6.5"/><path d="M1.5 8h13M2.6 4.5h10.8M2.6 11.5h10.8"/></g></svg>
            www.verodex.com
          </li>
        </ul>
      </div>
    </section>

    <section class="card card-logo" aria-label="Business card, brand side">
      <div class="brand">
        <span class="brand-dot"></span>
        <span class="brand-name">VERODEX</span>
      </div>
    </section>
  </main>
</body>
</html>
```